High end Electrical/home automation Business Card

Need a card for a high end electrical and home automation company utilising the existing logo.
Phone
Email
Website

Like black look with raised detail. Don’t necessarily need to keep colour of logo it could be made grayscale or white etc

Target Market(s)

High end clients

Contact Information for Business Card

Brightmoor Electrical

Requirements
Must have
• Logo, phone, email, website, address

High end look
Nice to have
• Black background card
Raised font
Should not have
• Lots of colour

```html
<!DOCTYPE html>
<html lang="en">
<head>
<meta charset="UTF-8">
<title>Brightmoor Electrical – Business Card</title>
<link href="https://fonts.googleapis.com/css2?family=Work+Sans:wght@400;500;700&display=swap" rel="stylesheet">
<style>
  :root {
    --stage: #1c1c1c;
    --card: #232323;
    --card-edge: #2b2b2b;
    --accent: #1591d6;
    --ink: #ffffff;
    --ink-soft: #e6e6e6;
  }
  * { margin: 0; padding: 0; box-sizing: border-box; }
  html, body {
    width: 1200px; height: 900px; overflow: hidden;
    background: var(--stage);
    font-family: "Work Sans", Arial, sans-serif;
  }
  .canvas {
    position: relative; width: 1200px; height: 900px;
    display: flex; flex-direction: column; align-items: center;
    justify-content: center; gap: 40px;
  }
  .card {
    position: relative; width: 660px; height: 380px;
    background: linear-gradient(135deg, var(--card) 0%, var(--card-edge) 100%);
    border-bottom: 6px solid var(--accent);
    box-shadow: 0 18px 40px rgba(0,0,0,0.55);
  }
  .brand {
    display: flex; align-items: center; gap: 14px;
    color: var(--ink); font-weight: 700; letter-spacing: -0.5px;
  }
  .brand-dot {
    width: 22px; height: 22px; border-radius: 50%;
    background: var(--accent); flex: none;
  }
  .card-front { display: flex; align-items: center; justify-content: center; }
  .card-front .brand { font-size: 40px; }
  .card-back { display: flex; align-items: center; padding: 0 40px 0 44px; }
  .card-back .brand { font-size: 30px; width: 290px; flex-wrap: wrap; }
  .divider {
    width: 2px; height: 210px; background: var(--accent);
    margin: 0 34px 0 22px; flex: none;
  }
  .contact { color: var(--ink-soft); font-size: 17px; line-height: 1.45; }
  .contact-name {
    color: var(--accent); font-weight: 500; font-size: 26px;
    letter-spacing: 3px; text-transform: uppercase; line-height: 1.1;
  }
  .contact-role { font-size: 17px; margin-bottom: 18px; }
  .contact-line { display: flex; align-items: center; gap: 8px; }
  .contact-line svg { width: 14px; height: 14px; flex: none; }
</style>
</head>
<body>
<main class="canvas">
  <section class="card card-front">
    <div class="brand"><span class="brand-dot"></span>Brightmoor Electrical</div>
  </section>

  <section class="card card-back">
    <div class="brand"><span class="brand-dot"></span>Brightmoor Electrical</div>
    <div class="divider"></div>
    <div class="contact">
      <p class="contact-name">Daniel Hartley</p>
      <p class="contact-role">Founder</p>
      <p>418 Larkspur Avenue</p>
      <p>Fernhill, WA 99120</p>
      <p class="contact-line">
        <svg viewBox="0 0 16 16" aria-hidden="true"><path d="M4 1.5l2.2 3-1.3 1.6c.8 1.8 2.2 3.2 4 4l1.6-1.3 3 2.2-1.3 2.5C7.4 13.3 2.7 8.6 1.5 3z" fill="#1591d6"/></svg>
        555 014 2273
      </p>
      <p class="contact-line">
        <svg viewBox="0 0 16 16" aria-hidden="true"><rect x="1.5" y="3.5" width="13" height="9" fill="none" stroke="#1591d6" stroke-width="1.4"/><path d="M1.5 3.5L8 9l6.5-5.5" fill="none" stroke="#1591d6" stroke-width="1.4"/></svg>
        hello@brightmoor.com
      </p>
      <p class="contact-line">
        <svg viewBox="0 0 16 16" aria-hidden="true"><circle cx="8" cy="8" r="6.3" fill="none" stroke="#1591d6" stroke-width="1.3"/><ellipse cx="8" cy="8" rx="2.8" ry="6.3" fill="none" stroke="#1591d6" stroke-width="1.1"/><path d="M1.7 8h12.6" stroke="#1591d6" stroke-width="1.1"/></svg>
        brightmoorelectrical.com
      </p>
    </div>
  </section>
</main>
</body>
</html>
```